Parcelwise HQ letterhead and envelope

Design a formal (8.5x11) letterhead and envelope for sales outreach and legal matters. Using design input from https://www.parcelwisehq.example/ and the attached documents.

Industry/Entity Type

Software Service

Requirements
Must have
• These 4 hex colors are our official colors:
• #355c98 [blue]
• #1eb1a2 [teal]
• #fdba12 [gold]
• #f1653b [orange]
• So no other colors besides these should be used.

```html
<!DOCTYPE html>
<html lang="en">
<head>
<meta charset="utf-8">
<title>Parcelwise HQ letterhead and envelope</title>
<link rel="stylesheet" href="https://fonts.googleapis.com/css2?family=Arimo:wght@700&family=Source+Sans+3:wght@400;600;700&display=swap">
<style>
  :root {
    --blue: #355c98;
    --teal: #1eb1a2;
    --gold: #fdba12;
    --orange: #f1653b;
    --paper: #ffffff;
    --backdrop: #ececec;
    --ink: #3a3a3a;
    --heading: #1d2a4a;
    --rule: #c9c9c9;
  }
  * { margin: 0; padding: 0; box-sizing: border-box; }
  html, body { width: 1200px; height: 825px; overflow: hidden; }
  body {
    position: relative;
    background: var(--backdrop);
    font-family: "Source Sans 3", Arial, sans-serif;
    color: var(--ink);
  }

  /* brand name with plain circle */
  .brand { display: flex; align-items: center; gap: 7px; color: var(--blue); }
  .brand-dot { width: 20px; height: 20px; border: 2.5px solid var(--blue); border-radius: 50%; }
  .brand-name { font-size: 20px; font-weight: 400; letter-spacing: 0.2px; line-height: 1; }

  /* footer band */
  .footer-band { position: absolute; left: 0; bottom: 0; width: 100%; height: 80px; display: block; }
  .footer-info { position: absolute; color: var(--paper); font-size: 7.2px; line-height: 11px; }
  .footer-company { color: var(--gold); font-weight: 700; font-size: 7.6px; }
  .footer-contacts span { margin-right: 6px; }
  .footer-contacts .icon { display: inline-block; width: 5px; height: 5px; border-radius: 50%; background: var(--gold); margin-right: 3px; }

  /* letterhead */
  .letterhead {
    position: absolute; left: 81px; top: 86px; width: 462px; height: 652px;
    background: var(--paper); overflow: hidden;
  }
  .letterhead .brand { position: absolute; left: 32px; top: 30px; }
  .decor-field {
    position: absolute; left: 30px; top: 470px; width: 400px; height: 110px;
    background: linear-gradient(120deg, rgba(241,101,59,0.025), rgba(30,177,162,0.025));
  }
  .salutation {
    position: absolute; left: 35px; top: 134px;
    font-family: "Arimo", Arial, sans-serif; font-weight: 700; font-size: 11.5px; color: var(--heading);
  }
  .letter-body { position: absolute; left: 35px; top: 160px; width: 392px; }
  .letter-body p { font-size: 9.6px; line-height: 12.1px; text-align: justify; margin-bottom: 12px; }
  .signature {
    position: absolute; left: 40px; top: 430px; width: 78px; height: 36px;
    background: linear-gradient(90deg, rgba(58,58,58,0.10), rgba(58,58,58,0.03));
    border-radius: 18px;
  }
  .letterhead .footer-info { left: 36px; top: 612px; }

  /* envelope */
  .envelope { position: absolute; left: 590px; top: 442px; width: 531px; height: 296px; }
  .envelope-flap { position: absolute; left: 0; top: 0; width: 531px; height: 67px; display: block; }
  .envelope-body {
    position: absolute; left: 0; top: 66px; width: 531px; height: 230px;
    background: var(--paper); overflow: hidden;
  }
  .envelope .brand { position: absolute; left: 36px; top: 24px; }
  .envelope .decor-field { left: 250px; top: 30px; width: 270px; height: 120px; }
  .address-window {
    position: absolute; left: 286px; top: 100px; width: 202px; height: 56px;
    background: var(--paper); padding: 14px 0 0 8px;
  }
  .address-window .line { height: 11px; border-bottom: 1px dotted var(--rule); width: 188px; }
  .envelope .footer-info { left: 39px; top: 190px; }
</style>
</head>
<body>
  <svg width="0" height="0" style="position:absolute">
    <defs>
      <linearGradient id="brandBand" x1="0" y1="0" x2="1" y2="0">
        <stop offset="0" stop-color="#355c98"/>
        <stop offset="1" stop-color="#1eb1a2"/>
      </linearGradient>
    </defs>
  </svg>

  <section class="letterhead" aria-label="Letterhead">
    <div class="brand"><span class="brand-dot"></span><span class="brand-name">Parcelwise HQ</span></div>
    <div class="decor-field" role="img" aria-label="Faint scattered line icons as background decoration"></div>

    <h1 class="salutation">Dear Mr. Carter,</h1>
    <div class="letter-body">
      <p>Lorem Ipsum is simply dummy text of the printing and typesetting industry. Lorem Ipsum has been the industry's standard dummy text ever since the 1500s, when an unknown printer took a galley of type and scrambled it to make a type specimen book. It has survived not only five centuries, but also the leap into electronic typesetting, remaining essentially unchanged.</p>
      <p>The standard chunk of Lorem Ipsum used since the 1500s is reproduced below for those interested. Sections 1.10.32 and 1.10.33 from "De Ratione Scribendi" by Aulus Venn are also reproduced in their exact original form, accompanied by English versions from the 1914 translation by H. Ashdown</p>
      <p>Lorem Ipsum is simply dummy text of the printing and typesetting industry. Lorem Ipsum has been the industry's standard dummy text ever since the 1500s, when an unknown printer took a galley of type and scrambled it to make a type specimen book. It has survived not only five centuries, but also the leap into electronic typesetting, remaining essentially unchanged. It was popularised in the</p>
      <p>The standard chunk of Lorem Ipsum used since the 1500s is reproduced below for those interested. Sections 1.10.32 and 1.10.33 from "De Ratione Scribendi" by Aulus Venn are also reproduced in their exact original form, accompanied by English versions from the 1914 translation by H. Ashdown</p>
    </div>
    <div class="signature" role="img" aria-label="Handwritten signature"></div>

    <svg class="footer-band" viewBox="0 0 462 80" preserveAspectRatio="none" aria-hidden="true">
      <path d="M0,16 C140,-6 250,54 340,52 C400,50 440,24 462,2" fill="none" stroke="#f1653b" stroke-width="3"/>
      <path d="M0,22 C140,0 250,60 340,58 C400,56 440,30 462,8 L462,80 L0,80 Z" fill="url(#brandBand)"/>
    </svg>
    <div class="footer-info">
      <div class="footer-company">Parcelwise HQ</div>
      <div>742 Harbor Lane Fairview, MI 48000</div>
      <div class="footer-contacts"><span><i class="icon"></i>(800) 555-0142</span><span><i class="icon"></i>jdoe@parcelwisehq.example</span><span><i class="icon"></i>www.parcelwisehq.example</span></div>
    </div>
  </section>

  <section class="envelope" aria-label="Envelope">
    <svg class="envelope-flap" viewBox="0 0 531 67" aria-hidden="true">
      <path d="M0,67 L8,40 C14,28 40,22 90,18 C200,10 250,-2 300,0 C360,2 440,22 510,28 C524,30 531,40 531,50 L531,67 Z" fill="url(#brandBand)"/>
    </svg>
    <div class="envelope-body">
      <div class="brand"><span class="brand-dot"></span><span class="brand-name">Parcelwise HQ</span></div>
      <div class="decor-field" role="img" aria-label="Faint scattered line icons as background decoration"></div>
      <div class="address-window">
        <div class="line"></div><div class="line"></div><div class="line"></div>
      </div>
      <svg class="footer-band" viewBox="0 0 531 80" preserveAspectRatio="none" aria-hidden="true">
        <path d="M0,16 C160,-6 290,54 390,52 C460,50 505,24 531,2" fill="none" stroke="#f1653b" stroke-width="3"/>
        <path d="M0,22 C160,0 290,60 390,58 C460,56 505,30 531,8 L531,80 L0,80 Z" fill="url(#brandBand)"/>
      </svg>
      <div class="footer-info">
        <div class="footer-company">Parcelwise HQ</div>
        <div>742 Harbor Lane Fairview, MI 48000</div>
        <div class="footer-contacts"><span><i class="icon"></i>(800) 555-0142</span><span><i class="icon"></i>jdoe@parcelwisehq.example</span><span><i class="icon"></i>www.parcelwisehq.example</span></div>
      </div>
    </div>
  </section>
</body>
</html>
```